BOLD & MINIMALIST DESIGN NEEDED

We want a very bold but minimalistic business card design that is impactful and utilizes both sides of the business card. Our current logo is included for your use.

We want bold fonts and good use of negative space. We don't want the logo to overpower the design.

Target Market(s)

Professionals who are building new commercial buildings.

Industry/Entity Type

Construction

Contact Information for Business Card

Name, Title, email, office phone, cell phone, website

Font styles to use
Serif
Sans Serif

Requirements
Must have
• Bold design!

```html
<!DOCTYPE html>
<html lang="en">
<head>
<meta charset="utf-8">
<title>Ridgeline Design + Build — Business Card</title>
<link rel="stylesheet" href="https://fonts.googleapis.com/css2?family=Montserrat:wght@400;500;800&family=Oswald:wght@600&display=swap">
<style>
  :root {
    --stage: #f3f3f1;
    --paper: #fbfbfa;
    --ink: #1c1c1c;
    --night: #1e1e1e;
    --green: #5fb42a;
    --mark-grey: #cfcfcf;
    --mark-green: #e3ecd3;
    --white: #ffffff;
    --muted: #8a8a8a;
  }
  * { box-sizing: border-box; margin: 0; padding: 0; }
  html, body { width: 1200px; height: 800px; overflow: hidden; }
  body {
    background: var(--stage);
    font-family: "Montserrat", Arial, sans-serif;
    color: var(--ink);
    position: relative;
  }
  .card {
    position: absolute;
    top: 245px;
    width: 540px;
    height: 310px;
    overflow: hidden;
    box-shadow: 0 2px 6px rgba(0,0,0,.12);
  }
  .card--front { left: 40px; background: var(--paper); }
  .card--back { left: 620px; background: var(--night); }

  .company {
    display: flex;
    align-items: center;
    gap: 8px;
    font-weight: 800;
    text-transform: uppercase;
    letter-spacing: .02em;
  }
  .company__square { width: 10px; height: 10px; background: currentColor; flex: none; }

  .card--front .company { position: absolute; left: 34px; top: 34px; font-size: 15px; color: var(--ink); }

  .person { position: absolute; left: 34px; top: 92px; }
  .person__name {
    font-family: "Oswald", "Arial Narrow", sans-serif;
    font-weight: 600;
    font-size: 28px;
    color: var(--green);
    text-transform: uppercase;
    line-height: 1;
  }
  .person__title { font-size: 11px; letter-spacing: .06em; margin-top: 4px; }

  .contact { position: absolute; left: 34px; top: 170px; list-style: none; font-size: 12px; }
  .contact__item { display: flex; align-items: center; gap: 8px; height: 20px; }
  .contact__icon { width: 12px; height: 12px; flex: none; }
  .contact__accent { color: var(--green); }

  .brand-mark-area {
    position: absolute;
    right: 40px;
    bottom: 28px;
    width: 190px;
    height: 190px;
    background: linear-gradient(135deg, var(--mark-green), var(--mark-grey));
  }

  .card--back .company {
    position: absolute;
    left: 0; right: 0; top: 132px;
    justify-content: center;
    font-size: 30px;
    color: var(--white);
  }
  .back-rule {
    position: absolute;
    left: 120px; right: 120px; top: 178px;
    height: 1px;
    background: var(--muted);
  }
</style>
</head>
<body>

<section class="card card--front" aria-label="Business card front">
  <div class="company"><span class="company__square"></span>Ridgeline Design + Build</div>

  <div class="person">
    <p class="person__name">Mark Delaney</p>
    <p class="person__title">OWNER</p>
  </div>

  <ul class="contact">
    <li class="contact__item">
      <svg class="contact__icon" viewBox="0 0 12 12" aria-hidden="true"><path d="M2.5 1h2l1 3-1.3 1a6 6 0 0 0 2.8 2.8L8 6.5l3 1v2c0 .8-.7 1.5-1.5 1.5A8.5 8.5 0 0 1 1 2.5C1 1.7 1.7 1 2.5 1z" fill="var(--green)"/></svg>
      (512) 448-2736
    </li>
    <li class="contact__item">
      <svg class="contact__icon" viewBox="0 0 12 12" aria-hidden="true"><rect x="1" y="5" width="10" height="6" rx="1" fill="var(--green)"/><path d="M1 4.5C3 1 9 1 11 4.5" stroke="var(--green)" stroke-width="1.6" fill="none"/></svg>
      (512) 448-2741
    </li>
    <li class="contact__item">
      <svg class="contact__icon" viewBox="0 0 12 12" aria-hidden="true"><rect x="1" y="2.5" width="10" height="7" fill="none" stroke="var(--green)" stroke-width="1.2"/><path d="M1 2.5l5 4 5-4" fill="none" stroke="var(--green)" stroke-width="1.2"/></svg>
      ridgelinebuild@mail.com
    </li>
    <li class="contact__item">
      <svg class="contact__icon" viewBox="0 0 12 12" aria-hidden="true"><circle cx="6" cy="6" r="5" fill="none" stroke="var(--green)" stroke-width="1.2"/><path d="M1 6h10M6 1c-2.5 3-2.5 7 0 10M6 1c2.5 3 2.5 7 0 10" fill="none" stroke="var(--green)" stroke-width="1"/></svg>
      <span>www.<span class="contact__accent">ridgelinebuild</span>.com</span>
    </li>
  </ul>

  <div class="brand-mark-area" role="img" aria-label="Large faint company monogram decoration"></div>
</section>

<section class="card card--back" aria-label="Business card back">
  <div class="company"><span class="company__square"></span>Ridgeline Design + Build</div>
  <div class="back-rule"></div>
</section>

</body>
</html>
```